Business Card for Industrial Distributor

We need a business card design for an industrial distributor. We sell machine parts for the manufacturing and oil industry. We would like the cards to look clean and modern but with a touch of industry.

Our colors are blue/white.

Please feel free to visit our website www.korvelpartsco.com

Target Market(s)

mexican manufacturers in the automobile/aerospace industry

Industry/Entity Type

Industrial

Colors
ffffff
0555a3

```html
<!DOCTYPE html>
<html lang="en">
<head>
<meta charset="utf-8">
<title>Korvel Parts – Business Card</title>
<link href="https://fonts.googleapis.com/css2?family=Open+Sans:wght@400;600;700&display=swap" rel="stylesheet">
<style>
  :root {
    --backdrop: #e9e9ec;
    --card-black: #0b0b0c;
    --brand-blue: #0555a3;
    --blue-light: #2b66c9;
    --blue-deep: #1b4fa5;
    --accent-blue: #2f6fd6;
    --white: #ffffff;
    --text-soft: #e8e8e8;
    --divider: rgba(255,255,255,0.12);
  }
  * { margin: 0; padding: 0; box-sizing: border-box; }
  html, body { width: 1200px; height: 900px; overflow: hidden; }
  body {
    background: var(--backdrop);
    font-family: "Open Sans", Arial, sans-serif;
    position: relative;
  }
  .card {
    position: absolute;
    width: 525px;
    height: 300px;
    top: 300px;
    border-radius: 4px;
    overflow: hidden;
    box-shadow: 0 6px 18px rgba(0,0,0,0.18);
  }
  /* back side: contact details */
  .card--back { left: 50px; background: var(--card-black); }
  .back__mark {
    position: absolute;
    left: 48px; top: 70px;
    width: 170px;
    text-align: center;
  }
  .back__circle {
    width: 130px; height: 130px;
    margin: 0 auto 14px;
    border-radius: 50%;
    background: radial-gradient(circle at 40% 35%, var(--accent-blue), var(--brand-blue));
  }
  .back__name {
    color: var(--white);
    font-weight: 700;
    font-size: 20px;
  }
  .contact {
    position: absolute;
    left: 270px; top: 50px;
    padding-left: 22px;
    border-left: 1px solid var(--divider);
    height: 150px;
  }
  .contact__name { color: var(--accent-blue); font-weight: 600; font-size: 16px; line-height: 1.1; }
  .contact__title { color: var(--text-soft); font-size: 12px; margin-bottom: 16px; }
  .contact__list { list-style: none; }
  .contact__item {
    display: flex; align-items: center; gap: 9px;
    color: var(--text-soft); font-size: 12.5px; line-height: 18px;
  }
  .contact__item svg { width: 10px; height: 10px; fill: var(--accent-blue); flex: none; }
  .contact__address {
    position: absolute;
    left: 292px; top: 212px;
    color: var(--text-soft); font-size: 13px; line-height: 19px;
  }
  /* front side: brand */
  .card--front {
    left: 625px;
    background: radial-gradient(ellipse at 50% 35%, var(--blue-light), var(--blue-deep) 75%);
  }
  .brand {
    position: absolute;
    left: 80px; top: 102px;
    display: flex; align-items: center; gap: 14px;
  }
  .brand__circle { width: 50px; height: 50px; border-radius: 50%; background: var(--white); }
  .brand__name { color: var(--white); font-weight: 700; font-size: 46px; letter-spacing: -0.5px; }
  .rule { position: absolute; height: 1px; background: rgba(255,255,255,0.75); }
  .rule--upper { left: 370px; right: 0; top: 172px; }
  .rule--lower { left: 0; width: 270px; top: 262px; }
  .front__url {
    position: absolute;
    left: 290px; top: 252px;
    color: var(--white); font-size: 12px; letter-spacing: 0.3px;
  }
</style>
</head>
<body>
  <section class="card card--back" aria-label="Business card back">
    <div class="back__mark">
      <div class="back__circle"></div>
      <div class="back__name">Korvel Parts</div>
    </div>
    <div class="contact">
      <p class="contact__name">Daniel Reyes</p>
      <p class="contact__title">Managing Director</p>
      <ul class="contact__list">
        <li class="contact__item"><svg viewBox="0 0 10 10"><path d="M1 3c0-1 1-2 2-2h4c1 0 2 1 2 2v1H7V3H3v1H1zM2 5h6l1 4H1z"/></svg>(044) 123 456 789</li>
        <li class="contact__item"><svg viewBox="0 0 10 10"><rect x="2.5" y="0.5" width="5" height="9" rx="1"/></svg>(044)123456789</li>
        <li class="contact__item"><svg viewBox="0 0 10 10"><path d="M0 2h10v6H0zM0 2l5 3.5L10 2" /></svg>info@youremail.com</li>
        <li class="contact__item"><svg viewBox="0 0 10 10"><circle cx="5" cy="5" r="4.5"/></svg>www.webname.com</li>
      </ul>
    </div>
    <p class="contact__address">12345,your address goes here,<br>country name,12345</p>
  </section>

  <section class="card card--front" aria-label="Business card front">
    <div class="brand">
      <span class="brand__circle"></span>
      <span class="brand__name">Korvel Parts</span>
    </div>
    <span class="rule rule--upper"></span>
    <span class="rule rule--lower"></span>
    <p class="front__url">www.korvelpartsco.com</p>
  </section>
</body>
</html>
```